I need a website designed. I am a mortgage loan officer and would like to have a website for me and my team where i can post resources, videos and blog information for my clients. A website like themorvaskteam.com .

The theme is - The Pelkins Team - Home Loan Group powered by Brightwell Home Loans -

Target Market(s)

B2B (Real Estate Agents)and B2C (Home buyers and refinancing)

Industry/Entity Type

Mortgage Lender

Coding

Coded - Design and coding required

Number of Pages Required

5+ page

Font styles to use
Serif
Sans Serif

Colors

Designer to choose colors to be used in the design.

Requirements
Must have
• Disclaimers: Licensed by the Bureau of Lending Affairs under the Pacific Credit Providers Act. Loans made or arranged pursuant to a Pacific Credit Providers Act License. Equal Housing Lender Brightwell Cannot Accept mortgage applications for properties located in New York via this site
• Mobile Friendly
Nice to have
• Main Links: Home, About Us(see team flyer), Mortgage 101, Contact Us (formzig form)

```html
<!DOCTYPE html>
<html lang="en">
<head>
<meta charset="utf-8">
<title>The Pelkins Team – Home Loan Group</title>
<link href="https://fonts.googleapis.com/css2?family=Raleway:wght@400;500;600;700&display=swap" rel="stylesheet">
<style>
:root{
  --blue:#1b6ea8;
  --blue-dark:#0a4f86;
  --ink:#222;
  --text:#555;
  --line:#222;
  --black:#050505;
  --white:#fff;
}
*{box-sizing:border-box;margin:0;padding:0}
html,body{width:1200px;height:3622px;overflow:hidden}
body{font-family:"Raleway",sans-serif;color:var(--text);background:var(--white);position:relative}
.section{position:absolute;left:0;width:1200px}
a{color:inherit;text-decoration:none}

/* header */
.site-header{top:0;height:138px}
.brand{position:absolute;left:88px;top:46px;display:flex;align-items:center;gap:12px}
.brand-mark{width:34px;height:34px;background:var(--blue)}
.brand-name{font-size:26px;font-weight:700;color:var(--blue);letter-spacing:.5px;text-transform:uppercase;white-space:nowrap}
.topbar{position:absolute;right:88px;top:24px;display:flex;align-items:center;gap:18px;font-size:15px;color:var(--ink)}
.topbar .item{display:flex;align-items:center;gap:9px}
.ico-circle{width:30px;height:30px;border:1.5px solid var(--blue);border-radius:50%;display:flex;align-items:center;justify-content:center}
.login{background:var(--blue);color:var(--white);border-radius:16px;padding:6px 18px;font-size:14px;font-weight:600}
.main-nav{position:absolute;right:88px;top:82px;display:flex;gap:56px;font-size:17px;font-weight:500;color:var(--ink)}
.main-nav .active{color:var(--blue)}

/* hero */
.hero{top:138px;height:524px}
.hero-photo{position:absolute;inset:0;background:linear-gradient(180deg,#7fa3c4 0%,#a9c0d3 30%,#8a7566 58%,#5d5044 78%,#3f4a36 100%)}
.hero-play{position:absolute;left:566px;top:168px;width:68px;height:68px;border-radius:50%;background:rgba(0,0,0,.55);display:flex;align-items:center;justify-content:center}
.hero-title{position:absolute;top:262px;width:100%;text-align:center;color:var(--white);font-size:56px;font-weight:500}
.hero-sub{position:absolute;top:338px;width:100%;text-align:center;color:var(--white);font-size:24px}
.hero-arrows{position:absolute;right:90px;top:462px;color:var(--white);font-size:18px;letter-spacing:14px}

/* welcome */
.welcome{top:662px;height:563px;text-align:center}
.section-title{font-size:34px;font-weight:500;color:var(--ink)}
.welcome .section-title{margin-top:80px}
.welcome-text{width:920px;margin:22px auto 0;font-size:13.5px;line-height:24px}
.features{position:absolute;top:256px;left:0;width:1200px}
.feature{position:absolute;width:260px;text-align:center}
.feature-icon{width:104px;height:104px;border-radius:50%;background:var(--blue);margin:0 auto;display:flex;align-items:center;justify-content:center}
.feature h3{margin-top:24px;font-size:21px;font-weight:500;color:var(--ink)}
.feature p{margin-top:10px;font-size:13.5px;line-height:22px}
.learn{display:block;margin-top:8px;font-size:12.5px;color:var(--blue)}

/* profile */
.profile{top:1225px;height:472px;color:var(--white);background:linear-gradient(135deg,#0a5fa6 0%,#1a7bc4 40%,#0c5a9c 70%,#0a4f86 100%)}
.profile-photo{position:absolute;left:145px;top:98px;width:260px;height:260px;border-radius:50%;border:5px solid var(--white);background:radial-gradient(circle at 50% 40%,#d9c1ad 0%,#8f96a3 60%,#3b4150 100%)}
.profile-body{position:absolute;left:487px;top:80px;width:600px}
.profile-body h2{font-size:34px;font-weight:500}
.profile-body .role{font-size:13px;margin-top:6px}
.profile-body .meta{font-size:13px;line-height:25px;margin-top:18px}
.profile-body .bio{font-size:13.5px;line-height:25px;margin-top:14px;text-align:justify}

/* resources */
.resources{top:1697px;height:656px;text-align:center}
.resources .section-title{margin-top:103px}
.card{position:absolute;top:178px;width:308px;height:368px;background:var(--white);box-shadow:0 4px 18px rgba(0,0,0,.18);text-align:center}
.card-photo{margin:12px;height:194px}
.card h3{margin-top:30px;font-size:19px;font-weight:500;color:var(--ink)}
.card p{margin:12px auto 0;width:260px;font-size:13.5px;line-height:22px}
.card .learn{margin-top:10px}

/* team */
.team{top:2353px;height:442px;background:linear-gradient(180deg,#7a7a7a,#666);color:var(--white);text-align:center}
.team .section-title{color:var(--white);margin-top:52px}
.member{position:absolute;top:162px;width:320px;text-align:center}
.member-photo{width:120px;height:120px;margin:0 auto;border-radius:50%;border:3px solid var(--white);background:radial-gradient(circle at 50% 40%,#cfb9a6,#51555f)}
.member h3{margin-top:28px;font-size:19px;font-weight:500}
.member p{font-size:13.5px;line-height:22px;margin-top:10px}

/* blog */
.blog{top:2795px;height:435px;text-align:center}
.blog .section-title{margin-top:70px}
.post{position:absolute;top:162px;width:500px;height:172px;background:var(--white);box-shadow:0 3px 14px rgba(0,0,0,.16);text-align:left;display:flex}
.post-photo{width:162px;height:172px;flex:none}
.post-body{padding:18px 22px}
.post-body h4{font-size:14px;font-weight:500;color:var(--ink)}
.post-body .date{font-size:12px;margin-top:8px;color:var(--ink)}
.post-body p{font-size:12.5px;line-height:19px;margin-top:6px;text-align:justify}
.post-body .learn{margin-top:6px}

/* footer */
.site-footer{top:3230px;height:392px;background:var(--black);color:var(--white)}
.footer-brand{position:absolute;left:88px;top:92px;display:flex;align-items:center;gap:10px}
.footer-brand .brand-mark{width:26px;height:26px}
.footer-brand .brand-name{font-size:20px}
.fcol{position:absolute;top:66px;font-size:12.5px}
.fcol h5{font-size:13px;font-weight:600;letter-spacing:.5px;margin-bottom:22px;text-transform:uppercase}
.fcol li{list-style:none;display:flex;gap:12px;margin-bottom:12px;line-height:18px}
.subscribe{display:flex;margin-top:14px}
.subscribe .field{width:150px;height:30px;background:var(--white);color:#aaa;font-size:11px;padding:8px}
.subscribe .btn{height:30px;background:var(--blue);padding:8px 14px;font-size:12px}
.socials{display:flex;gap:14px}
.socials span{width:25px;height:25px;background:var(--white);border-radius:4px}
.copyright{position:absolute;top:248px;width:100%;text-align:center;font-size:12.5px}
.divider{position:absolute;top:284px;left:88px;right:88px;height:1px;background:var(--line)}
.disclaimer{position:absolute;top:318px;left:160px;width:880px;text-align:center;font-size:12px;line-height:24px}
</style>
</head>
<body>

<header class="section site-header">
  <div class="brand"><span class="brand-mark"></span><span class="brand-name">The Pelkins Team</span></div>
  <div class="topbar">
    <span class="item"><span class="ico-circle"><svg width="14" height="14" viewBox="0 0 24 24"><path fill="#1b6ea8" d="M6.6 10.8a15 15 0 0 0 6.6 6.6l2.2-2.2c.3-.3.7-.4 1-.2 1.1.4 2.3.6 3.6.6.6 0 1 .4 1 1V20c0 .6-.4 1-1 1A17 17 0 0 1 3 4c0-.6.4-1 1-1h3.5c.6 0 1 .4 1 1 0 1.3.2 2.5.6 3.6.1.3 0 .7-.2 1z"/></svg></span>203-555-0147</span>
    <span class="item"><span class="ico-circle"><svg width="14" height="12" viewBox="0 0 24 18"><rect x="1" y="1" width="22" height="16" rx="2" fill="none" stroke="#1b6ea8" stroke-width="2"/><path d="M1 2l11 8 11-8" fill="none" stroke="#1b6ea8" stroke-width="2"/></svg></span>info@pelkinsteam.com</span>
    <a class="login">&#9679; Login</a>
  </div>
  <nav class="main-nav"><a class="active">Home</a><a>About us</a><a>Mortgage 101</a><a>Contact us</a></nav>
</header>

<section class="section hero">
  <div class="hero-photo" role="img" aria-label="Photo of a two-storey suburban home with garage under a blue sky"></div>
  <div class="hero-play"><svg width="26" height="28" viewBox="0 0 26 28"><path d="M3 2l21 12L3 26z" fill="#fff"/></svg></div>
  <h1 class="hero-title">Pelkins Team</h1>
  <p class="hero-sub">Neque porro quisquam est qui &nbsp;dolorem</p>
  <div class="hero-arrows">&lsaquo;&rsaquo;</div>
</section>

<section class="section welcome">
  <h2 class="section-title">Welcome to The Pelkins Team</h2>
  <p class="welcome-text">It is a long established fact that a reader will be distracted by the readable content of a page when looking at its layout. The point of using Lorem Ipsum is that it has a more-or-less normal distribution of letters, as opposed to using 'Content here, content here', making it look like readable English. Many desktop publishing packages and web page editors now use Lorem Ipsum as their default model text.</p>
  <div class="features">
    <div class="feature" style="left:150px">
      <div class="feature-icon"><svg width="40" height="36" viewBox="0 0 24 22"><path d="M12 1L1 11h3v10h6v-6h4v6h6V11h3z" fill="#fff"/></svg></div>
      <h3>Porro Quisquam</h3>
      <p>It is a long established fact that a<br>reader will be distracted by the</p>
      <a class="learn">Learn More &rarr;</a>
    </div>
    <div class="feature" style="left:470px">
      <div class="feature-icon"><svg width="44" height="34" viewBox="0 0 26 20"><rect x="4" y="2" width="18" height="12" rx="1" fill="none" stroke="#fff" stroke-width="2"/><path d="M1 16h24v2H1z" fill="#fff"/></svg></div>
      <h3>Dolorem Ipsum</h3>
      <p>It is a long established fact that a<br>reader will be distracted by the</p>
      <a class="learn">Learn More &rarr;</a>
    </div>
    <div class="feature" style="left:770px">
      <div class="feature-icon"><svg width="40" height="40" viewBox="0 0 24 24"><path d="M22 2L2 10l7 3 2 8 3-6 5 4z" fill="#fff"/></svg></div>
      <h3>Neque Porro</h3>
      <p>It is a long established fact that a<br>reader will be distracted by the</p>
      <a class="learn">Learn More &rarr;</a>
    </div>
  </div>
</section>

<section class="section profile">
  <div class="profile-photo" role="img" aria-label="Portrait of Owen Pelkins, senior branch lead"></div>
  <div class="profile-body">
    <h2>Owen Pelkins</h2>
    <p class="role">Senior Branch Lead</p>
    <p class="meta">Brightwell Home Loans, Inc – NMLS 40217, Owen.Pelkins@brightwellhomeloans.com<br>Office: (407) 555-0190 Fax: (855) 555-0133</p>
    <p class="bio">For more than a decade I have helped families plan and finance their homes. My goal is a simple, clear loan process with no surprises along the way. I will walk you through every step, answer each question, and keep you informed until the day you get your keys. Our team has earned the Summit Service award and a place in the Leaders Circle for service, and we have proudly helped hundreds of local families move into homes of their own over the past several years.</p>
  </div>
</section>

<section class="section resources">
  <h2 class="section-title">Resources</h2>
  <article class="card" style="left:90px">
    <div class="card-photo" role="img" aria-label="Photo of a couple meeting a loan advisor at a desk" style="background:linear-gradient(135deg,#e9edf0,#b7c2cc 60%,#8a7f78)"></div>
    <h3>Dolorem Ipsum</h3>
    <p>The point of using Lorem Ipsum is that it has a more-or-less normal</p>
    <a class="learn">Read More &rsaquo;</a>
  </article>
  <article class="card" style="left:446px">
    <div class="card-photo" role="img" aria-label="Photo of a hand holding a small model house" style="background:linear-gradient(135deg,#1c3550,#35607f 55%,#c98866)"></div>
    <h3>Quisquam est qui</h3>
    <p>The point of using Lorem Ipsum is that it has a more-or-less normal</p>
    <a class="learn">Read More &rsaquo;</a>
  </article>
  <article class="card" style="left:802px">
    <div class="card-photo" role="img" aria-label="Photo of a couple shaking hands with an agent outside a home" style="background:linear-gradient(135deg,#8f9e8a,#c9b8a4 55%,#6e5f55)"></div>
    <h3>Ipsum quia dolor</h3>
    <p>The point of using Lorem Ipsum is that it has a more-or-less normal</p>
    <a class="learn">Read More &rsaquo;</a>
  </article>
</section>

<section class="section team">
  <h2 class="section-title">My Team</h2>
  <div class="member" style="left:85px">
    <div class="member-photo" role="img" aria-label="Portrait of Marco Telles"></div>
    <h3>Marco Telles</h3>
    <p>Loan Partner I – NMLS ID 1730518<br>Marco.Telles@brightwellhomeloans.com<br>(407) 555-0172</p>
  </div>
  <div class="member" style="left:440px">
    <div class="member-photo" role="img" aria-label="Portrait of Luis Andrade"></div>
    <h3>Luis Andrade</h3>
    <p>Loan Processor – NMLS ID 1492260<br>Luis.Andrade@brightwellhomeloans.com<br>(407) 555-0194</p>
  </div>
  <div class="member" style="left:785px">
    <div class="member-photo" role="img" aria-label="Portrait of Greta Hollis"></div>
    <h3>Greta Hollis</h3>
    <p>Closing Coordinator/Team Leader<br>Greta.Hollis@brightwellhomeloans.com<br>(631) 555-0151</p>
  </div>
</section>

<section class="section blog">
  <h2 class="section-title">Latest Blog</h2>
  <article class="post" style="left:93px">
    <div class="post-photo" role="img" aria-label="Photo of small model houses on a table" style="background:linear-gradient(135deg,#f1ece6,#c9574a 55%,#e6e1da)"></div>
    <div class="post-body">
      <h4>Nemo Enim Ipsam Volup</h4>
      <p class="date">09-07-2017</p>
      <p>Lorem Ipsum has been the industry's standard dummy text ever since the 1500s, when an unknown printer took a galley</p>
      <a class="learn">Read More &gt;&gt;</a>
    </div>
  </article>
  <article class="post" style="left:617px">
    <div class="post-photo" role="img" aria-label="Photo of a model house next to a calculator" style="background:linear-gradient(135deg,#5c4a3d,#b89c80 55%,#ddd2c4)"></div>
    <div class="post-body">
      <h4>Nemo Enim Ipsam Volup</h4>
      <p class="date">09-07-2017</p>
      <p>Lorem Ipsum has been the industry's standard dummy text ever since the 1500s, when an unknown printer took a galley</p>
      <a class="learn">Read More &gt;&gt;</a>
    </div>
  </article>
</section>

<footer class="section site-footer">
  <div class="footer-brand"><span class="brand-mark"></span><span class="brand-name">The Pelkins Team</span></div>
  <div class="fcol" style="left:368px">
    <h5>Contact Us</h5>
    <ul>
      <li><span>&#9679;</span><span>Suite 210, 4480 Harbor Lane<br>NW, Westfield, AB</span></li>
      <li><span>&#9742;</span><span>(587) 555-0107</span></li>
      <li><span>&#9993;</span><span>info@pelkinsteam.com</span></li>
    </ul>
  </div>
  <div class="fcol" style="left:650px">
    <h5>Join Our Mailing List</h5>
    <p>Your about us information would fit<br>here nicely.</p>
    <div class="subscribe"><span class="field">Email address</span><span class="btn">Submit</span></div>
  </div>
  <div class="fcol" style="left:955px">
    <h5>Follow Us Out There</h5>
    <div class="socials"><span></span><span></span><span></span><span></span></div>
  </div>
  <p class="copyright">Copyright © 2018. All Rights Reserved</p>
  <div class="divider"></div>
  <p class="disclaimer">Licensed by the Bureau of Lending Affairs under the Pacific Credit Providers Act. Loans made or arranged pursuant to a Pacific Credit Providers Act License. Equal Housing Lender Brightwell Cannot Accept mortgage applications for properties located in New York via this site</p>
</footer>

</body>
</html>
```